20 year old business card needs re-design

We need to redesign our corporate business card look. We need something that appears more modern, eye catchy but professional.

Target Market(s)

manufacturing industry

Industry/Entity Type

Manufacturer

Contact Information for Business Card

One side can have the logo. Other side can have contact information.

Font styles to use
Serif

Colors
3277b5
33b8a4
ffffff

Requirements
Must have
• Eye catchy - need to standout from the crowd. company logo cannot change. Full name, job title, phone number and email address.
Should not have
• Fax, business address is not necessary.

```html
<!DOCTYPE html>
<html lang="en">
<head>
<meta charset="utf-8">
<title>Kestrel Forge – Business Card</title>
<link rel="stylesheet" href="https://fonts.googleapis.com/css2?family=Tinos:wght@400;700&display=swap">
<style>
  :root {
    --brand-blue: #3277b5;
    --brand-teal: #33b8a4;
    --ink: #1c1c1c;
    --band-dark: #1f1c1e;
    --card: #ffffff;
    --backdrop: #e4e4e6;
  }
  * { box-sizing: border-box; margin: 0; padding: 0; }
  html, body {
    width: 1200px; height: 880px; overflow: hidden;
    background: var(--backdrop);
    font-family: "Tinos", "Times New Roman", serif;
    color: var(--ink);
  }
  .canvas { position: relative; width: 1200px; height: 880px; }
  .card {
    position: absolute; width: 600px; height: 343px;
    background: var(--card);
    box-shadow: 0 6px 18px rgba(0,0,0,.18);
    overflow: hidden;
  }
  /* Front side */
  .card--front { left: 50px; top: 70px; }
  .brand {
    display: flex; align-items: center; gap: 12px;
    font-weight: 700; color: var(--ink); letter-spacing: -0.5px;
    white-space: nowrap;
  }
  .brand__mark { background: var(--brand-blue); flex: none; }
  .card--front .brand {
    position: absolute; left: 0; right: 0; top: 120px;
    justify-content: center; font-size: 56px;
  }
  .card--front .brand__mark { width: 34px; height: 34px; }
  .front__web {
    position: absolute; left: 0; right: 0; top: 232px;
    text-align: center; font-size: 19px; font-weight: 700;
    color: var(--brand-blue);
  }
  /* Back side */
  .card--back { left: 550px; top: 440px; }
  .card--back .brand {
    position: absolute; right: 34px; top: 34px; font-size: 40px;
  }
  .card--back .brand__mark { width: 24px; height: 24px; }
  .person { position: absolute; left: 34px; top: 108px; }
  .person__name { font-size: 23px; font-weight: 700; color: var(--brand-blue); line-height: 1.05; }
  .person__title { font-size: 16px; line-height: 1.2; }
  .tagline {
    position: absolute; left: 34px; top: 190px;
    font-size: 14px; line-height: 1.15;
  }
  .locations {
    position: absolute; right: 34px; top: 172px;
    text-align: right; font-size: 14px; line-height: 1.2;
  }
  .locations__cert { color: var(--brand-blue); margin-top: 2px; }
  .divider {
    position: absolute; left: 34px; right: 34px; top: 232px;
    height: 1px; background: var(--brand-blue);
  }
  .contacts { position: absolute; left: 34px; top: 246px; list-style: none; }
  .contacts li {
    display: flex; align-items: center; gap: 10px;
    font-size: 16px; line-height: 1; height: 24px;
  }
  .contacts svg { width: 16px; height: 16px; flex: none; }
  .base-band {
    position: absolute; left: 0; right: 0; bottom: 0; height: 12px;
    background: var(--band-dark);
  }
  .base-band__accent {
    position: absolute; left: 0; bottom: 0; width: 200px; height: 12px;
    background: var(--brand-teal);
  }
</style>
</head>
<body>
<main class="canvas">
  <section class="card card--front" aria-label="Card front">
    <div class="brand"><span class="brand__mark"></span>Kestrel Forge</div>
    <p class="front__web">KestrelForge.com</p>
  </section>

  <section class="card card--back" aria-label="Card back">
    <div class="brand"><span class="brand__mark"></span>Kestrel Forge</div>

    <div class="person">
      <p class="person__name">Dan Merrick</p>
      <p class="person__title">Senior Project Manager</p>
    </div>

    <p class="tagline">International manufacturing solutions<br>for OEM customers in North America</p>

    <div class="locations">
      <p>Offices &amp; Warehousing:</p>
      <p>USA - Taiwan - Mexico</p>
      <p class="locations__cert">TS16949 &amp; ISO9001 Certified Facilities</p>
    </div>

    <div class="divider"></div>

    <ul class="contacts">
      <li>
        <svg viewBox="0 0 16 16" aria-hidden="true"><rect width="16" height="16" fill="var(--brand-blue)"/><path d="M4 5c0-1 1-1.5 2-1.5l.8 2-1 .8c.5 1.2 1.4 2.1 2.6 2.6l.8-1 2 .8c0 1-.5 2-1.5 2C6.5 10.7 4 8.3 4 5z" fill="#fff"/></svg>
        <span>555-014-2200 xt 201</span>
      </li>
      <li>
        <svg viewBox="0 0 16 16" aria-hidden="true"><rect width="16" height="16" fill="var(--brand-blue)"/><rect x="3" y="4.5" width="10" height="7" fill="#fff"/><path d="M3 4.5l5 4 5-4" fill="none" stroke="var(--brand-blue)" stroke-width="1"/></svg>
        <span>dan@kestrelforge.com</span>
      </li>
    </ul>

    <div class="base-band"><div class="base-band__accent"></div></div>
  </section>
</main>
</body>
</html>
```